Postcard Design Project A Healthy reminder

Dr.'s Dhelpit and Sirel dunwat. Internal Medicine/Family practice. This postcard will be for our patients that we have not seen in a while. Also we need another postcard (the one your designing) with a different heading for New patient's. Do you offer a price break for that? The only thing we would need to change is the heading. Please let me know. Thank you so much! Also can you use the map on the last postcard and our logo I made? I cant find it. Please feel free to call me or email me.

```html
<!DOCTYPE html>
<html lang="en">
<head>
<meta charset="utf-8">
<title>A Healthy Reminder – Postcard</title>
<link rel="stylesheet" href="https://fonts.googleapis.com/css2?family=Fira+Sans+Condensed:wght@600;700&family=Lato:wght@400;700&display=swap">
<style>
  :root {
    --stage: #4a4a4a;
    --red: #c8161d;
    --black: #111111;
    --ink: #1b1b1b;
    --white: #ffffff;
    --panel: #ececee;
    --photo-a: #d9c9b4;
    --photo-b: #8f8a86;
    --map-a: #eef0ea;
    --map-b: #d4d8cf;
    --line: #222222;
    --stamp: #e4e4e6;
    --social: #3b5b9a;
  }
  * { margin: 0; padding: 0; box-sizing: border-box; }
  html, body { width: 1200px; height: 1200px; overflow: hidden; }
  body { background: var(--stage); position: relative; font-family: "Lato", sans-serif; color: var(--ink); }

  .postcard { position: absolute; width: 696px; height: 472px; background: var(--white); overflow: hidden; }
  .postcard--front { left: 81px; top: 108px; }
  .postcard--back { left: 428px; top: 625px; }
  .postcard svg.shapes { position: absolute; inset: 0; }

  .brand { position: absolute; text-align: center; }
  .brand__name { display: flex; align-items: center; justify-content: center; gap: 7px; font-weight: 700; color: var(--ink); white-space: nowrap; }
  .brand__mark { width: 12px; height: 12px; background: var(--red); }
  .brand__tagline { font-weight: 700; color: var(--ink); }

  .front__brand { left: 40px; top: 70px; width: 230px; }
  .front__brand .brand__name { font-size: 17px; }
  .front__brand .brand__tagline { font-size: 8px; margin-top: 36px; }

  .headline { position: absolute; left: 27px; top: 186px; font-family: "Fira Sans Condensed", sans-serif; line-height: 1.12; }
  .headline__lead { color: var(--red); font-weight: 700; font-size: 31px; text-transform: uppercase; }
  .headline__rest { color: var(--black); font-weight: 600; font-size: 32px; }

  .phone-pill { position: absolute; display: flex; align-items: center; gap: 10px; background: var(--red); color: var(--white); border-radius: 999px; }
  .phone-pill svg { flex: none; }
  .front__phone { left: 27px; top: 312px; width: 239px; height: 44px; padding-left: 16px; font-size: 23px; }
  .back__phone { left: 26px; top: 310px; width: 185px; height: 35px; padding-left: 14px; font-size: 17px; }

  .contact { position: absolute; color: var(--white); font-size: 15px; line-height: 19px; }
  .contact__row { display: flex; align-items: flex-start; gap: 9px; }
  .front__contact { left: 30px; top: 382px; }
  .front__contact .contact__row + .contact__row { margin-top: 5px; }

  .back__address { position: absolute; left: 28px; top: 360px; font-size: 13.5px; line-height: 17px; color: var(--ink); }
  .back__web { position: absolute; left: 28px; top: 410px; color: var(--white); font-size: 13px; line-height: 20px; }
  .social-dot { width: 10px; height: 10px; background: var(--social); margin-top: 5px; flex: none; }

  .mission { position: absolute; left: 26px; top: 22px; width: 300px; }
  .mission__title { font-family: "Fira Sans Condensed", sans-serif; font-weight: 600; color: var(--red); font-size: 31px; line-height: 38px; }
  .mission__text { font-size: 11px; line-height: 13.7px; color: var(--ink); margin-top: 9px; }
  .mission__text + .mission__text { margin-top: 13px; }

  .back__brand { left: 375px; top: 58px; width: 170px; }
  .back__brand .brand__name { font-size: 12.5px; gap: 5px; }
  .back__brand .brand__mark { width: 9px; height: 9px; }
  .back__brand .brand__tagline { font-size: 6px; margin-top: 26px; }

  .stamp-box { position: absolute; left: 598px; top: 28px; width: 70px; height: 70px; background: var(--stamp); }
  .address-lines { position: absolute; left: 500px; top: 197px; width: 168px; }
  .address-lines span { display: block; height: 2px; background: var(--line); margin-bottom: 31px; }
</style>
</head>
<body>

<section class="postcard postcard--front" aria-label="Postcard front">
  <svg class="shapes" viewBox="0 0 696 472" width="696" height="472" aria-hidden="true">
    <defs>
      <linearGradient id="photoTone" x1="0" y1="0" x2="1" y2="1">
        <stop offset="0" stop-color="var(--photo-a)"/>
        <stop offset="1" stop-color="var(--photo-b)"/>
      </linearGradient>
    </defs>
    <rect x="0" y="372" width="696" height="100" fill="var(--black)"/>
    <path d="M372 0 C332 150 334 330 428 472 L700 472 L700 0 Z" fill="var(--white)"/>
    <path d="M376 0 C336 150 338 330 432 472" fill="none" stroke="var(--red)" stroke-width="9"/>
    <path d="M390 0 C352 150 352 330 446 472" fill="none" stroke="var(--black)" stroke-width="7"/>
  </svg>
  <svg class="shapes" viewBox="0 0 696 472" width="696" height="472" role="img" aria-label="Photograph of two doctors in white coats reviewing a chart in a clinic hallway">
    <path d="M402 0 C364 150 364 330 458 472 L696 472 L696 0 Z" fill="url(#photoTone)"/>
  </svg>

  <div class="brand front__brand">
    <div class="brand__name"><span class="brand__mark"></span>Dhelpit T Dunwat, M.D.</div>
    <div class="brand__tagline">A Primary Care Office</div>
  </div>

  <h1 class="headline">
    <span class="headline__lead">A Healthy Remainder</span><br>
    <span class="headline__rest">it is time for your<br>annual exam</span>
  </h1>

  <div class="phone-pill front__phone">
    <svg width="20" height="20" viewBox="0 0 20 20" aria-hidden="true"><circle cx="10" cy="10" r="8.5" fill="none" stroke="#fff" stroke-width="1.6"/><path d="M7 5.5l1.6 2.4-1 1c.6 1.3 1.6 2.3 2.9 2.9l1-1 2.4 1.6-.9 1.6c-3.5-.4-6.6-3.5-7-7z" fill="#fff"/></svg>
    <span>(555) 014-2286</span>
  </div>

  <div class="contact front__contact">
    <div class="contact__row">
      <svg width="12" height="16" viewBox="0 0 12 16" aria-hidden="true"><path d="M6 0a6 6 0 0 0-6 6c0 4.5 6 10 6 10s6-5.5 6-10a6 6 0 0 0-6-6z" fill="var(--red)"/><circle cx="6" cy="6" r="2.2" fill="var(--black)"/></svg>
      <span>4120 N. Larkmoor Street Suite 210<br>Westhollow, Ca 93999</span>
    </div>
    <div class="contact__row">
      <svg width="12" height="12" viewBox="0 0 12 12" aria-hidden="true" style="margin-top:4px"><circle cx="6" cy="6" r="5.2" fill="none" stroke="var(--red)" stroke-width="1.4"/><path d="M.8 6h10.4M6 .8c-2.8 3-2.8 7.4 0 10.4M6 .8c2.8 3 2.8 7.4 0 10.4" fill="none" stroke="var(--red)" stroke-width="1.1"/></svg>
      <span>www.dunwatmd.com</span>
    </div>
  </div>
</section>

<section class="postcard postcard--back" aria-label="Postcard back">
  <svg class="shapes" viewBox="0 0 696 472" width="696" height="472" aria-hidden="true">
    <defs>
      <clipPath id="panelClip">
        <path d="M0 0 L335 0 C360 150 370 300 275 472 L0 472 Z"/>
      </clipPath>
    </defs>
    <path d="M0 0 L335 0 C360 150 370 300 275 472 L0 472 Z" fill="var(--panel)"/>
    <rect x="0" y="401" width="400" height="71" fill="var(--black)" clip-path="url(#panelClip)"/>
    <path d="M338 0 C363 150 373 300 278 472" fill="none" stroke="var(--red)" stroke-width="8"/>
    <path d="M351 0 C376 150 386 300 291 472" fill="none" stroke="var(--black)" stroke-width="6"/>
    <circle cx="331" cy="353" r="70" fill="var(--white)"/>
    <circle cx="331" cy="353" r="65" fill="none" stroke="var(--red)" stroke-width="5"/>
  </svg>
  <svg class="shapes" viewBox="0 0 696 472" width="696" height="472" role="img" aria-label="Street map showing the office location">
    <defs>
      <linearGradient id="mapTone" x1="0" y1="0" x2="1" y2="1">
        <stop offset="0" stop-color="var(--map-a)"/>
        <stop offset="1" stop-color="var(--map-b)"/>
      </linearGradient>
    </defs>
    <circle cx="331" cy="353" r="62" fill="url(#mapTone)"/>
  </svg>

  <div class="mission">
    <h2 class="mission__title">Our Mission</h2>
    <p class="mission__text">Our office is committed to working with each individual patient to achieve and maintain their optimal wellbeing. We strive to deliver high quality, compassionate care. We are committed to offering affordable medical services to patients in an atmosphere of respect, professionalism and confidentiality.</p>
    <p class="mission__text">Our Physicians and healthcare staff are dedicated to providing thorough, informative healthcare. We promise our patients to keep them up to date, educated, and informed. We are confident our care is of the utmost quality, and the needs of our patients will always be our first priority.</p>
    <p class="mission__text">We look forward to working together closely<br>towards a healthier future</p>
  </div>

  <div class="phone-pill back__phone">
    <svg width="15" height="15" viewBox="0 0 20 20" aria-hidden="true"><circle cx="10" cy="10" r="8.5" fill="none" stroke="#fff" stroke-width="1.8"/><path d="M7 5.5l1.6 2.4-1 1c.6 1.3 1.6 2.3 2.9 2.9l1-1 2.4 1.6-.9 1.6c-3.5-.4-6.6-3.5-7-7z" fill="#fff"/></svg>
    <span>(555) 014-2286</span>
  </div>

  <div class="back__address contact__row">
    <svg width="10" height="14" viewBox="0 0 12 16" aria-hidden="true" style="margin-top:2px"><path d="M6 0a6 6 0 0 0-6 6c0 4.5 6 10 6 10s6-5.5 6-10a6 6 0 0 0-6-6z" fill="var(--red)"/><circle cx="6" cy="6" r="2.2" fill="var(--panel)"/></svg>
    <span>4120 N. Larkmoor Street Suite 210<br>Westhollow, Ca 93999</span>
  </div>

  <div class="back__web">
    <div class="contact__row">
      <svg width="10" height="10" viewBox="0 0 12 12" aria-hidden="true" style="margin-top:5px"><circle cx="6" cy="6" r="5.2" fill="none" stroke="var(--red)" stroke-width="1.4"/><path d="M.8 6h10.4M6 .8c-2.8 3-2.8 7.4 0 10.4M6 .8c2.8 3 2.8 7.4 0 10.4" fill="none" stroke="var(--red)" stroke-width="1.1"/></svg>
      <span>www.dunwatmd.com</span>
    </div>
    <div class="contact__row">
      <span class="social-dot"></span>
      <span>visit us on social</span>
    </div>
  </div>

  <div class="brand back__brand">
    <div class="brand__name"><span class="brand__mark"></span>Dhelpit T Dunwat, M.D.</div>
    <div class="brand__tagline">A Primary Care Office</div>
  </div>

  <div class="stamp-box" aria-hidden="true"></div>
  <div class="address-lines" aria-hidden="true"><span></span><span></span><span></span></div>
</section>

</body>
</html>
```